Business Card for Multi-Brand Sportswear Company

We are looking for a business card which represents our company and the multiple brands within it.

The company: Fen Athletics (LTD)
The brands: Fen, TavaPuni, ElmStretch, Grit and Rain

Employees using these cards would be representing Fen Athletics, rather than any of the individual brands. You will see a current design within the uploaded files, to give some inspiration. The actual text of the brands is not necessary, but the logos should be on there is some format.

Our creative minds on this are stretched, so we are looking for someone to make this their own, and show us what a good business card should look like.

We may like to get these printed with spot gloss, so keep that in mind with your designs.

www.fenathletics.co.uk

Industry/Entity Type

Business

Contact Information for Business Card

Leo Pemberton-Hale
Operations Manager
(+44) 1632 960 418
Leo@fenathletics.co.uk
www.fenathletics.co.uk

Font styles to use
Sans Serif
Other font styles liked:
• Eurostile

Colors
ffffff

Requirements
Nice to have
• Dark (black) background

```html
<!DOCTYPE html>
<html lang="en">
<head>
<meta charset="utf-8">
<title>Fen Athletics – Business Card</title>
<link rel="stylesheet" href="https://fonts.googleapis.com/css2?family=Michroma&family=Open+Sans:wght@400;600;700&display=swap">
<style>
  :root {
    --red: #e8202a;
    --black: #0d0d0d;
    --white: #ffffff;
    --paper: #f7f7f7;
    --ink: #2a2a2a;
    --grey: #8a8a8a;
    --backdrop: #e6e3df;
    --tile-purple: #5e5366;
  }
  * { margin: 0; padding: 0; box-sizing: border-box; }
  html, body { width: 1200px; height: 900px; overflow: hidden; }
  body {
    background: var(--backdrop);
    font-family: "Open Sans", Arial, sans-serif;
    position: relative;
  }
  .card {
    position: absolute;
    width: 540px;
    height: 310px;
    overflow: hidden;
    box-shadow: 0 6px 18px rgba(0,0,0,0.18);
  }

  /* ---------- Back of card ---------- */
  .card-back {
    left: 50px;
    top: 170px;
    background: var(--red);
  }
  .card-back .brand-band {
    position: absolute;
    left: 0; right: 0;
    top: 150px;
    height: 92px;
    background: var(--black);
  }
  .wordmark {
    position: absolute;
    display: flex;
    flex-direction: column;
    align-items: flex-end;
  }
  .wordmark .name {
    font-family: "Michroma", "Open Sans", sans-serif;
    font-size: 30px;
    letter-spacing: 1px;
    line-height: 1;
    white-space: nowrap;
  }
  .wordmark .tagline {
    font-family: "Michroma", "Open Sans", sans-serif;
    font-size: 7px;
    letter-spacing: 3px;
    margin-top: 6px;
  }
  .card-back .wordmark { left: 120px; top: 95px; }
  .card-back .wordmark .name { color: var(--white); }
  .card-back .wordmark .tagline { color: var(--black); }

  .brand-row {
    position: absolute;
    left: 110px; right: 30px;
    top: 178px;
    display: flex;
    align-items: center;
    justify-content: space-between;
  }
  .brand {
    display: flex;
    align-items: center;
    gap: 6px;
    font-family: "Open Sans", Arial, sans-serif;
    font-weight: 600;
    font-size: 13px;
    white-space: nowrap;
  }
  .brand .mark-square {
    width: 26px; height: 26px;
    background: var(--tile-purple);
    border-radius: 3px;
  }
  .brand .mark-square.red { background: var(--red); }
  .brand .mark-circle {
    width: 24px; height: 24px;
    border: 2px solid var(--grey);
    border-radius: 50%;
  }
  .brand-tavapuni { color: #cfc8d6; }
  .brand-grit { color: var(--red); }
  .brand-fen { color: var(--white); }
  .brand-elm { color: var(--grey); }

  /* ---------- Front of card ---------- */
  .card-front {
    left: 610px;
    top: 420px;
    background: var(--paper);
  }
  .card-front .swoosh {
    position: absolute;
    left: 0; top: 0;
    width: 540px; height: 310px;
  }
  .holder {
    position: absolute;
    left: 34px; top: 38px;
  }
  .holder .person {
    color: var(--red);
    font-weight: 700;
    font-size: 19px;
    line-height: 1.1;
    white-space: nowrap;
  }
  .holder .role {
    color: var(--ink);
    font-weight: 600;
    font-size: 15px;
    margin-top: 2px;
  }
  .card-front .wordmark { right: 34px; top: 44px; }
  .card-front .wordmark .name { color: var(--black); font-size: 26px; }
  .card-front .wordmark .tagline { color: var(--ink); }

  .contact-list {
    position: absolute;
    left: 34px; top: 172px;
    list-style: none;
  }
  .contact-list li {
    display: flex;
    align-items: center;
    gap: 9px;
    color: var(--ink);
    font-size: 15px;
    line-height: 25px;
    white-space: nowrap;
  }
  .contact-list svg { width: 12px; height: 12px; fill: var(--red); flex: none; }

  .address {
    position: absolute;
    right: 22px; bottom: 30px;
    color: var(--white);
    font-size: 12.5px;
    letter-spacing: 0.2px;
    white-space: nowrap;
  }
</style>
</head>
<body>

  <!-- Back of card -->
  <section class="card card-back" aria-label="Business card, back">
    <div class="brand-band"></div>
    <div class="wordmark">
      <span class="name">Fen Athletics</span>
      <span class="tagline">PERFORMANCE WEAR</span>
    </div>
    <div class="brand-row">
      <div class="brand brand-tavapuni"><span class="mark-square"></span>TavaPuni</div>
      <div class="brand brand-grit"><span class="mark-square red"></span>Grit and Rain</div>
      <div class="brand brand-fen">Fen</div>
      <div class="brand brand-elm"><span class="mark-circle"></span>ElmStretch</div>
    </div>
  </section>

  <!-- Front of card -->
  <section class="card card-front" aria-label="Business card, front">
    <svg class="swoosh" viewBox="0 0 540 310" aria-hidden="true">
      <path fill="var(--red)" d="M0,250 C140,292 290,245 420,165 C310,248 160,300 0,286 Z"/>
      <path fill="var(--black)" d="M0,282 C160,300 300,250 400,190 C450,162 500,150 540,146 L540,310 L0,310 Z"/>
    </svg>

    <div class="holder">
      <p class="person">Leo Pemberton-Hale</p>
      <p class="role">Operations Manager</p>
    </div>

    <div class="wordmark">
      <span class="name">Fen Athletics</span>
      <span class="tagline">PERFORMANCE WEAR</span>
    </div>

    <ul class="contact-list">
      <li>
        <svg viewBox="0 0 12 12" aria-hidden="true"><path d="M1 3 Q1 1 3 1 L9 1 Q11 1 11 3 L11 4 L8 4 L8 3 L4 3 L4 4 L1 4 Z M2 6 L10 6 L11 11 L1 11 Z"/></svg>
        +44(0)1632 960418
      </li>
      <li>
        <svg viewBox="0 0 12 12" aria-hidden="true"><path d="M0 2 L12 2 L12 10 L0 10 Z M1 3 L6 7 L11 3 Z" fill-rule="evenodd"/></svg>
        leo@fenathletics.co.uk
      </li>
      <li>
        <svg viewBox="0 0 12 12" aria-hidden="true"><circle cx="6" cy="6" r="5.5"/></svg>
        www.fenathletics.co.uk
      </li>
    </ul>

    <p class="address">Reed Park,Marshby,Fenwick,FN7 3AH</p>
  </section>

</body>
</html>
```